Ferncrest Roam Wording For Logo & Business card

I have the logo, I just need the "Ferncrest Roam" wording to go with it, and a business card design. The only thing on the business card is the website info. We provide nature connection experiences, and bolster these efforts through writing and host a platform for community around it.

I also have an idea of what it could look like (sketch), though I'm really not sure how it would come out. I am open to the best design and happy to consider original artwork. You can see what the site is about at FerncrestRoam.example.

Contact Information for Business Card

The only thing on the business card is the website info and the design. I will put other messaging on the back.

Website lettering (FerncrestRoam.example) in Montserrat

Logo Text

Ferncrest Roam (letters optional)

Font styles to use
Other font styles liked:
• montserrat

```html
<!DOCTYPE html>
<html lang="en">
<head>
<meta charset="utf-8">
<title>Ferncrest Roam – Logo Wording &amp; Business Card</title>
<link rel="stylesheet" href="https://fonts.googleapis.com/css2?family=Montserrat:wght@400;500;600;700&display=swap">
<style>
  :root {
    --backdrop: #6e6e70;
    --purple: #5b3a72;
    --purple-deep: #3a2150;
    --orange: #e2571c;
    --cream: #f4ecd4;
    --paper: #f7f6f4;
    --ink: #3d3547;
  }
  * { box-sizing: border-box; margin: 0; padding: 0; }
  html, body { width: 1200px; height: 863px; overflow: hidden; }
  body {
    position: relative;
    background: var(--backdrop);
    font-family: "Montserrat", sans-serif;
  }

  /* Logo lockup: plain circle + name */
  .lockup { position: absolute; display: flex; align-items: center; gap: 14px; }
  .lockup__dot { border-radius: 50%; flex: none; }
  .lockup__name { font-weight: 700; letter-spacing: 0.02em; line-height: 1; white-space: nowrap; }

  .lockup--backdrop { left: 780px; top: 80px; }
  .lockup--backdrop .lockup__dot { width: 90px; height: 90px; background: var(--purple-deep); }
  .lockup--backdrop .lockup__name { font-size: 30px; color: var(--cream); }

  .corner-badge {
    position: absolute; left: -500px; top: 540px;
    width: 920px; height: 920px; border-radius: 50%;
    background: #ffffff;
  }
  .lockup--corner { left: 26px; top: 730px; }
  .lockup--corner .lockup__dot { width: 86px; height: 86px; background: var(--purple-deep); }
  .lockup--corner .lockup__name { font-size: 26px; color: var(--purple-deep); }

  /* Card front */
  .card { position: absolute; width: 480px; height: 274px; border-radius: 3px; overflow: hidden; box-shadow: 0 10px 24px rgba(0,0,0,0.35); }
  .card--front { left: 140px; top: 160px; background: var(--purple); }
  .card--front .lockup { left: 60px; top: 100px; }
  .card--front .lockup__dot { width: 76px; height: 76px; background: var(--purple-deep); }
  .card--front .lockup__name { font-size: 30px; color: var(--cream); }

  /* Card back */
  .card--back { left: 575px; top: 410px; width: 500px; height: 286px; background: var(--paper); }
  .card--back .lockup { left: 26px; top: 72px; gap: 10px; }
  .card--back .lockup__dot { width: 52px; height: 52px; background: var(--purple-deep); }
  .card--back .lockup__name { font-size: 17px; color: var(--purple-deep); }
  .card__divider { position: absolute; left: 252px; top: 52px; width: 1px; height: 96px; background: #9c97a3; }
  .card__details { position: absolute; left: 270px; top: 58px; color: var(--ink); }
  .card__name { font-size: 18px; font-weight: 700; color: var(--purple-deep); letter-spacing: 0.03em; }
  .card__role { font-size: 13px; font-weight: 600; color: var(--orange); margin-top: 2px; }
  .card__web { display: flex; align-items: center; gap: 7px; font-size: 12px; margin-top: 18px; }
  .card__web svg { width: 9px; height: 9px; fill: var(--orange); flex: none; }
  .card__wave { position: absolute; left: 0; bottom: 0; width: 500px; height: 286px; }
</style>
</head>
<body>

  <div class="lockup lockup--backdrop">
    <span class="lockup__dot"></span>
    <span class="lockup__name">Ferncrest Roam</span>
  </div>

  <section class="card card--front" aria-label="Business card front">
    <div class="lockup">
      <span class="lockup__dot"></span>
      <span class="lockup__name">Ferncrest Roam</span>
    </div>
  </section>

  <section class="card card--back" aria-label="Business card back">
    <svg class="card__wave" viewBox="0 0 500 286" aria-hidden="true">
      <path d="M0 178 C120 250 300 262 500 238 L500 286 L0 286 Z" fill="var(--orange)"/>
      <path d="M0 194 C120 262 300 270 500 246 L500 286 L0 286 Z" fill="var(--paper)"/>
      <path d="M0 200 C130 268 310 276 500 250 L500 286 L0 286 Z" fill="var(--purple-deep)"/>
    </svg>
    <div class="lockup">
      <span class="lockup__dot"></span>
      <span class="lockup__name">Ferncrest Roam</span>
    </div>
    <div class="card__divider"></div>
    <div class="card__details">
      <p class="card__name">DANA HOLLOWAY, MA</p>
      <p class="card__role">Founder</p>
      <p class="card__web"><svg viewBox="0 0 10 10" aria-hidden="true"><circle cx="5" cy="5" r="4.8"/></svg>www.ferncrestroam.example</p>
    </div>
  </section>

  <div class="corner-badge"></div>
  <div class="lockup lockup--corner">
    <span class="lockup__dot"></span>
    <span class="lockup__name">Ferncrest Roam</span>
  </div>

</body>
</html>
```